I need a sophisticated and powerful book cover design that combines Japanese minimalism with contemporary appeal. The cover should convey personal transformation through the metaphor of a katana (Japanese sword).
Key Design Elements:
A katana, either partially shown or artistically rendered
Subtle Japanese design elements without being stereotypical
Clean, minimalist aesthetic
Professional font selection that bridges Eastern and Western typography
Color scheme: Deep blacks, steel grays, and possibly a touch of red or gold for accent
Mood/Style:
Professional and sophisticated
Blend of traditional Japanese aesthetics with modern design
Should appeal to personal development and business readers
Must convey strength and transformation
Elegant rather than aggressive
Specific Requirements:
Title: "The Lantern Compass"
Subtitle: "Quiet Methods for Growing Inner Steadiness and Calm Endurance"
Author names: Dorvelan Thaske and Meloda Thaske
Cover dimensions: Standard hardcover book size (6" x 9")
Must work well in both physical and digital thumbnail formats
Should be striking and legible when viewed as a small image online
Design Specifics:
Japanese elements such as brushstroke effects, kanji characters, or wave patterns
The design should reflect the book's core message: personal transformation through Japanese wisdom principles, using the katana as a metaphor for growth and development.

```html
<!DOCTYPE html>
<html lang="en">
<head>
<meta charset="utf-8">
<title>The Lantern Compass — Book Cover</title>
<link rel="stylesheet" href="https://fonts.googleapis.com/css2?family=Montserrat:wght@500;600;700&family=Potta+One&display=swap">
<style>
  :root {
    --backdrop: #000000;
    --paper: #ffffff;
    --ink: #0d0d0d;
    --accent-red: #ed1c24;
    --accent-red-soft: #f0494b;
  }
  * { margin: 0; padding: 0; box-sizing: border-box; }
  html, body {
    width: 1200px;
    height: 1200px;
    overflow: hidden;
    background: var(--backdrop);
  }
  .canvas {
    position: relative;
    width: 1200px;
    height: 1200px;
    background: var(--backdrop);
  }
  .book-cover {
    position: absolute;
    left: 240px;
    top: 60px;
    width: 720px;
    height: 1080px;
    background: var(--paper);
    overflow: hidden;
  }
  .title {
    position: absolute;
    left: 0;
    top: 0;
    width: 720px;
    height: 320px;
    font-weight: normal;
  }
  .title span {
    position: absolute;
    display: block;
    left: 0;
    width: 720px;
    text-align: center;
    white-space: nowrap;
  }
  .title-article {
    top: 38px;
    font-family: "Montserrat", sans-serif;
    font-weight: 700;
    font-size: 80px;
    line-height: 80px;
    letter-spacing: 10px;
    text-indent: 10px;
    color: var(--ink);
  }
  .title-brush {
    top: 108px;
    font-family: "Potta One", sans-serif;
    font-size: 108px;
    line-height: 128px;
    color: var(--accent-red);
  }
  .title-main {
    top: 219px;
    font-family: "Montserrat", sans-serif;
    font-weight: 600;
    font-size: 112px;
    line-height: 112px;
    letter-spacing: 2px;
    color: var(--accent-red);
  }
  .subtitle {
    position: absolute;
    top: 334px;
    left: 100px;
    width: 520px;
    text-align: center;
    font-family: "Montserrat", sans-serif;
    font-weight: 500;
    font-size: 26px;
    line-height: 34px;
    letter-spacing: 0.6px;
    color: var(--ink);
  }
  .cover-art {
    position: absolute;
    left: 180px;
    top: 450px;
    width: 340px;
    height: 494px;
    background:
      linear-gradient(to bottom, #d9d9d9, #9a9a9a) 180px 10px / 18px 484px no-repeat,
      radial-gradient(circle at 50% 160px, var(--accent-red-soft) 0%, var(--accent-red) 140px, rgba(237, 28, 36, 0) 158px) 0 0 / 340px 330px no-repeat;
  }
  .author-band {
    position: absolute;
    left: 0;
    bottom: 0;
    width: 100%;
    height: 115px;
    background: var(--accent-red);
    display: flex;
    align-items: center;
    justify-content: center;
  }
  .author-names {
    font-family: "Montserrat", sans-serif;
    font-weight: 500;
    font-size: 35px;
    letter-spacing: 0.5px;
    color: var(--paper);
    white-space: nowrap;
  }
</style>
</head>
<body>
  <div class="canvas">
    <article class="book-cover">
      <h1 class="title">
        <span class="title-article">THE</span>
        <span class="title-brush">LANTERN</span>
        <span class="title-main">COMPASS</span>
      </h1>
      <p class="subtitle">Quiet Methods for Growing Inner Steadiness and Calm Endurance</p>
      <div class="cover-art" role="img" aria-label="Illustration of a katana standing vertically over a red brushstroke sun with cherry blossom branches"></div>
      <footer class="author-band">
        <p class="author-names">Dorvelan Thaske &amp; Meloda Thaske</p>
      </footer>
    </article>
  </div>
</body>
</html>
```